Brightmoor Talent company

We require a website for job recruitment company called "Brightmoor Talent"
Our company is specialising in recruitment of skilled labour from Sri Lanka into Australian market.
We would like to include a job advertising plugin where jobs can be listed and applied for .
COPYWRITING MUST BE INCLUDED !

Industry/Entity Type

Recruitment

Coding

Coded - Design and coding required

Number of Pages Required

5+ page

Colors

Designer to choose colors to be used in the design.

```html
<!DOCTYPE html>
<html lang="en">
<head>
<meta charset="utf-8">
<title>Brightmoor Talent</title>
<link href="https://fonts.googleapis.com/css2?family=Libre+Caslon+Text:wght@700&family=Roboto:wght@400;500;700&display=swap" rel="stylesheet">
<style>
:root{
  --blue:#0a4ea3;
  --blue-dark:#073b82;
  --blue-deep:#062f6c;
  --ink:#222;
  --text:#666;
  --grey:#ececef;
  --white:#fff;
  --serif:"Libre Caslon Text",Georgia,serif;
  --sans:"Roboto",Arial,sans-serif;
}
*{margin:0;padding:0;box-sizing:border-box}
html,body{width:1200px;height:3694px;overflow:hidden}
body{position:relative;font-family:var(--sans);color:var(--ink);background:var(--white)}
.abs{position:absolute}
.photo{position:absolute}

/* header */
.navbar{left:65px;top:26px;width:1071px;height:79px;background:var(--white);border-radius:40px;z-index:5}
.brand{position:absolute;left:83px;top:16px;font-family:var(--serif);font-size:26px;color:#555;line-height:1}
.brand span{display:block;color:var(--blue);font-size:17px;letter-spacing:4px;margin-top:4px;margin-left:38px}
.nav-link{position:absolute;top:32px;font-size:13.5px;font-weight:700;color:var(--ink)}
.nav-link.active{color:var(--blue)}
.btn-apply{position:absolute;left:844px;top:15px;width:181px;height:48px;border-radius:24px;background:var(--blue);color:#fff;font-size:13.5px;font-weight:700;display:flex;align-items:center;justify-content:center}

/* hero */
.hero{left:0;top:0;width:1200px;height:685px;background:linear-gradient(100deg,#0b3f8c 0%,#2a5fa8 40%,#7a8fa8 60%,#b9b4ad 80%,#8d8a86 100%)}
.hero-shade{left:0;top:0;width:1200px;height:685px;background:linear-gradient(90deg,rgba(8,55,130,.85) 0%,rgba(8,55,130,.55) 45%,rgba(8,55,130,0) 70%)}
.eyebrow{font-size:14px;letter-spacing:4px;font-weight:500}
.hero .eyebrow{position:absolute;left:110px;top:239px;color:#fff}
.hero-title{left:110px;top:270px;font-family:var(--serif);font-size:52px;color:#fff;line-height:1.1;white-space:nowrap}
.hero-text{left:110px;top:345px;width:480px;font-size:14px;line-height:26px;color:#fff}
.btn-white{left:110px;top:417px;width:181px;height:48px;border-radius:24px;background:#fff;color:var(--blue);font-size:14px;font-weight:700;display:flex;align-items:center;justify-content:center}
.dots{left:110px;top:536px;display:flex;gap:4px}
.dots i{width:12px;height:12px;border-radius:50%;background:#fff;display:block}

/* service cards */
.services-bg{left:0;top:685px;width:1200px;height:488px;background:linear-gradient(180deg,#f4f4f6,#dcdde2)}
.service-card{top:619px;width:320px;height:451px;background:#fff;text-align:center}
.service-card .photo{left:9px;top:9px;width:308px;height:232px}
.service-card h3{position:absolute;top:262px;width:100%;font-size:20px;font-weight:500}
.service-card p{position:absolute;top:300px;left:26px;width:268px;font-size:13.5px;line-height:26px;color:var(--text)}
.arrow-pill{position:absolute;top:396px;left:125px;width:76px;height:27px;border-radius:14px;background:var(--blue);display:flex;align-items:center;justify-content:center}

/* about */
.about-accent{left:112px;top:1549px;width:40px;height:124px;background:var(--blue);border-radius:6px}
.about-photo{left:138px;top:1276px;width:418px;height:425px;border-radius:6px;background:linear-gradient(135deg,#d8d4cf,#8d8b89 55%,#4a4540)}
.section-label{color:var(--blue)}
.about .section-label{position:absolute;left:599px;top:1272px}
.about-title{left:597px;top:1306px;font-family:var(--serif);font-size:40px;color:var(--ink);white-space:nowrap}
.body-copy{font-size:13.5px;line-height:25.8px;color:var(--text);text-align:justify}
.about-p1{left:599px;top:1375px;width:490px}
.about-p2{left:599px;top:1530px;width:490px}
.btn-blue{background:var(--blue);color:#fff;font-weight:700;font-size:13.5px;border-radius:24px;display:flex;align-items:center;justify-content:center;gap:6px}
.about-btn{left:598px;top:1651px;width:181px;height:48px}

/* news */
.news{left:0;top:1803px;width:1200px;height:701px;background:var(--blue)}
.news .eyebrow{position:absolute;top:65px;width:100%;text-align:center;color:#fff}
.news-title{position:absolute;top:95px;width:100%;text-align:center;font-family:var(--serif);font-size:56px;color:#fff}
.news-feature{left:112px;top:2009px;width:545px;height:396px;border-radius:6px;background:linear-gradient(120deg,#b7b3ad,#e2dfdb 45%,#8f8b86)}
.news-tab{left:479px;top:1992px;width:195px;height:80px;background:#fff;border-radius:6px}
.news-list{left:545px;top:2061px;width:545px;height:593px;background:#fff;border-radius:6px;box-shadow:0 6px 24px rgba(0,0,0,.12)}
.news-item{position:absolute;left:30px;width:480px;height:157px}
.news-item .photo{left:0;top:0;width:209px;height:157px;border-radius:6px;background:linear-gradient(135deg,#6b4a33,#b98a5d 50%,#3b2a20)}
.news-date{position:absolute;left:240px;top:16px;font-size:13.5px;color:#999;display:flex;align-items:center;gap:6px}
.news-item h4{position:absolute;left:235px;top:46px;width:240px;font-size:20px;line-height:30px;font-weight:700;color:var(--blue-deep)}

/* why */
.why .section-label{position:absolute;left:108px;top:2703px}
.why-title{left:108px;top:2740px;font-family:var(--serif);font-size:33px;line-height:51px;color:var(--ink);z-index:2;white-space:nowrap}
.why-copy{left:112px;top:2855px;width:489px}
.feature{display:flex;align-items:center;gap:11px;width:240px}
.feature .ico{width:66px;height:66px;border-radius:50%;background:var(--blue);display:flex;align-items:center;justify-content:center;flex:none}
.feature span{font-size:16px;font-weight:500;line-height:26px;color:var(--ink)}
.why-photo{left:660px;top:2749px;width:428px;height:430px;background:linear-gradient(90deg,rgba(255,255,255,0) 0%,#e8e6e3 10%,#d8d6d3 60%,#c9c6c2 100%);z-index:1}

/* footer */
.footer{left:0;top:3281px;width:1200px;height:413px;background:linear-gradient(160deg,#0a4ea3,#0b3f8f)}
.footer-brand{position:absolute;left:143px;top:82px;font-family:var(--serif);font-size:34px;color:#fff;line-height:1}
.footer-brand span{display:block;font-size:19px;letter-spacing:4px;margin-top:6px;margin-left:40px}
.footer-about{position:absolute;left:143px;top:173px;width:216px;font-size:13.5px;line-height:26px;color:#fff;text-align:justify}
.footer h5{position:absolute;top:82px;font-size:22px;font-weight:500;color:#fff}
.footer ul{position:absolute;top:140px;list-style:none;font-size:13.5px;line-height:25.8px;color:#fff}
.contact-row{position:absolute;left:873px;display:flex;gap:22px;font-size:13.5px;line-height:25.8px;color:#fff;width:240px}
.contact-row svg{flex:none;margin-top:6px}
.copyright{position:absolute;top:348px;width:100%;text-align:center;font-size:13.5px;color:#fff}
</style>
</head>
<body>

<!-- hero -->
<section class="hero abs">
  <div class="photo" role="img" aria-label="Smiling young man in a white shirt celebrating in an office, colleagues reviewing papers in the background" style="left:0;top:0;width:1200px;height:685px;background:radial-gradient(ellipse at 72% 35%,rgba(230,220,210,.55),rgba(0,0,0,0) 45%)"></div>
  <div class="hero-shade abs"></div>
  <p class="eyebrow">WELCOME TO</p>
  <h1 class="hero-title abs">BRIGHTMOOR TALENT</h1>
  <p class="hero-text abs">Lorem ipsum dolor sit amet, consectetur adipiscing elit, sed do eiusmod tempor incididunt ut labore et dolore magna aliqua.</p>
  <a class="btn-white abs">GET STARTED</a>
  <div class="dots abs"><i></i><i></i><i></i><i></i></div>
</section>

<header class="navbar abs">
  <div class="brand">Brightmoor<span>Talent</span></div>
  <a class="nav-link active" style="left:387px">HOME</a>
  <a class="nav-link" style="left:457px">ABOUT US</a>
  <a class="nav-link" style="left:556px">SERVICES</a>
  <a class="nav-link" style="left:652px">BLOG</a>
  <a class="nav-link" style="left:718px">CONTACT US</a>
  <a class="btn-apply">APPLY TO JOBS</a>
</header>

<!-- services -->
<div class="services-bg abs"></div>
<div class="abs" style="left:120px;top:619px;width:960px;height:451px;background:#fff"></div>
<article class="service-card abs" style="left:120px">
  <div class="photo" role="img" aria-label="Print workers operating machinery in a workshop" style="background:linear-gradient(135deg,#c7ccd3,#6e7f93 55%,#2e3c50)"></div>
  <h3>Nemo enim ipsam</h3>
  <p>Lorem ipsum dolor sit amet, consectetur adipiscing elit, sed do eiusmod tempor incididunt ut labore</p>
  <span class="arrow-pill"><svg width="30" height="12" viewBox="0 0 30 12"><path d="M1 6h27M22 1l6 5-6 5" stroke="#fff" stroke-width="2" fill="none"/></svg></span>
</article>
<article class="service-card abs" style="left:438px">
  <div class="photo" role="img" aria-label="Worker in a hard hat standing in a factory" style="background:linear-gradient(135deg,#5b4a3a,#a88e6d 50%,#3a2f26)"></div>
  <h3>Nemo enim ipsam</h3>
  <p>Lorem ipsum dolor sit amet, consectetur adipiscing elit, sed do eiusmod tempor incididunt ut labore</p>
  <span class="arrow-pill"><svg width="30" height="12" viewBox="0 0 30 12"><path d="M1 6h27M22 1l6 5-6 5" stroke="#fff" stroke-width="2" fill="none"/></svg></span>
</article>
<article class="service-card abs" style="left:756px">
  <div class="photo" role="img" aria-label="Carpenter with ear protection cutting wood at a saw" style="background:linear-gradient(135deg,#2f5aa0,#6f7fa0 50%,#b89a72)"></div>
  <h3>Nemo enim ipsam</h3>
  <p>Lorem ipsum dolor sit amet, consectetur adipiscing elit, sed do eiusmod tempor incididunt ut labore</p>
  <span class="arrow-pill"><svg width="30" height="12" viewBox="0 0 30 12"><path d="M1 6h27M22 1l6 5-6 5" stroke="#fff" stroke-width="2" fill="none"/></svg></span>
</article>

<!-- about -->
<section class="about">
  <div class="about-accent abs"></div>
  <div class="about-photo abs" role="img" aria-label="Smiling businesswoman in glasses reading documents at a desk"></div>
  <p class="eyebrow section-label">ABOUT US</p>
  <h2 class="about-title abs">BRIGHTMOOR TALENT</h2>
  <p class="body-copy about-p1 abs">Lorem ipsum dolor sit amet, consectetur adipiscing elit, sed do eiusmod tempor incididunt ut labore et dolore magna aliqua. Ut enim ad minim veniam, quis nostrud exercitation ullamco laboris nisi ut aliquip ex ea commodo consequat. Duis aute irure dolor in reprehenderit in voluptate velit esse cillum dolore eu fugiat nulla pariatur.</p>
  <p class="body-copy about-p2 abs">Excepteur sint occaecat cupidatat non proident, sunt in culpa qui officia deserunt mollit anim id est laborum. Lorem ipsum dolor sit amet, consectetur adipiscing elit, sed do eiusmod tempor incididunt ut labore et dolore magna aliqua.</p>
  <a class="btn-blue about-btn abs">LEARN MORE <svg width="12" height="12" viewBox="0 0 12 12"><circle cx="6" cy="6" r="6" fill="#fff"/><path d="M5 3l3 3-3 3" stroke="#0a4ea3" stroke-width="1.8" fill="none"/></svg></a>
</section>

<!-- news -->
<section class="news abs">
  <p class="eyebrow">NEWS</p>
  <h2 class="news-title">LATEST NEWS</h2>
</section>
<div class="news-tab abs"></div>
<div class="news-feature abs" role="img" aria-label="Cheerful team celebrating with a woman giving two thumbs up"></div>
<div class="news-list abs">
  <div class="news-item" style="top:34px">
    <div class="photo" role="img" aria-label="Potter shaping clay in a workshop"></div>
    <p class="news-date"><svg width="13" height="13" viewBox="0 0 13 13"><rect x="1" y="2" width="11" height="10" rx="1" fill="none" stroke="#aaa" stroke-width="1.4"/><path d="M1 5h11M4 1v2M9 1v2" stroke="#aaa" stroke-width="1.4"/></svg>Jan 20, 2022</p>
    <h4>Lorem ipsum dolor sit amet, consectetur adi piscing</h4>
  </div>
  <div class="news-item" style="top:223px">
    <div class="photo" role="img" aria-label="Smiling craftswoman working with wood"></div>
    <p class="news-date"><svg width="13" height="13" viewBox="0 0 13 13"><rect x="1" y="2" width="11" height="10" rx="1" fill="none" stroke="#aaa" stroke-width="1.4"/><path d="M1 5h11M4 1v2M9 1v2" stroke="#aaa" stroke-width="1.4"/></svg>Jan 20, 2022</p>
    <h4>Lorem ipsum dolor sit amet, consectetur adi piscing</h4>
  </div>
  <div class="news-item" style="top:411px">
    <div class="photo" role="img" aria-label="Artisan at a pottery wheel in a studio"></div>
    <p class="news-date"><svg width="13" height="13" viewBox="0 0 13 13"><rect x="1" y="2" width="11" height="10" rx="1" fill="none" stroke="#aaa" stroke-width="1.4"/><path d="M1 5h11M4 1v2M9 1v2" stroke="#aaa" stroke-width="1.4"/></svg>Jan 20, 2022</p>
    <h4>Lorem ipsum dolor sit amet, consectetur adi piscing</h4>
  </div>
</div>

<!-- why choose us -->
<section class="why">
  <p class="eyebrow section-label">WHY CHOOSE US</p>
  <div class="why-photo abs" role="img" aria-label="Overhead view of two professionals shaking hands across a desk with a laptop and contract"></div>
  <h2 class="why-title abs">GET 12,000+ JOB SPACE<br>TALENTED PEOPLE IN HERE.</h2>
  <p class="body-copy why-copy abs">Lorem ipsum dolor sit amet, consectetur adipiscing elit, sed do eiusmod tempor incididunt ut labore et dolore magna aliqua. Ut enim ad minim veniam, quis nostrud exercitation ullamco laboris nisi ut aliquip ex ea commodo consequat. Duis aute irure dolor in reprehenderit in voluptate velit esse cillum dolore eu fugiat nulla pariatur.</p>
  <div class="feature abs" style="left:112px;top:3008px"><span class="ico"><svg width="34" height="34" viewBox="0 0 34 34" fill="none" stroke="#fff" stroke-width="1.6"><rect x="7" y="4" width="18" height="24" rx="2"/><path d="M11 10h10M11 14h6"/><circle cx="20" cy="20" r="5"/><path d="M24 24l5 5"/></svg></span><span>Search Millions<br>Jobs</span></div>
  <div class="feature abs" style="left:360px;top:3008px"><span class="ico"><svg width="34" height="34" viewBox="0 0 34 34" fill="none" stroke="#fff" stroke-width="1.6"><path d="M5 29h24M8 29v-6h6v6M14 29V17h6v12M20 29V10h6v19"/><circle cx="23" cy="5" r="2"/></svg></span><span>Top and Best<br>Career</span></div>
  <div class="feature abs" style="left:112px;top:3112px"><span class="ico"><svg width="34" height="34" viewBox="0 0 34 34" fill="none" stroke="#fff" stroke-width="1.6"><path d="M17 28s-8-8-8-14a8 8 0 0116 0c0 6-8 14-8 14z"/><circle cx="17" cy="14" r="3"/><path d="M5 30l6-6M29 30l-6-6"/></svg></span><span>Location Base<br>Search</span></div>
  <div class="feature abs" style="left:360px;top:3112px"><span class="ico"><svg width="34" height="34" viewBox="0 0 34 34" fill="none" stroke="#fff" stroke-width="1.6"><rect x="8" y="5" width="18" height="24" rx="2"/><circle cx="17" cy="14" r="4"/><path d="M12 24h10M12 20h10"/></svg></span><span>Recruiter<br>Directory</span></div>
</section>

<!-- footer -->
<footer class="footer abs">
  <div class="footer-brand">Brightmoor<span>Talent</span></div>
  <p class="footer-about">Lorem ipsum dolor sit amet, consectetur adipiscing elit, sed do eiusmod tempor incididunt ut labore et dolore magna</p>
  <h5 style="left:472px">Quick Links</h5>
  <ul style="left:472px"><li>Home</li><li>About us</li><li>Services</li><li>Blog</li><li>Reviews</li><li>Contact us</li></ul>
  <h5 style="left:673px">Resources</h5>
  <ul style="left:673px"><li>White papers</li><li>Events</li><li>Case Studies</li><li>Blog</li><li>Webinars</li><li>Q&amp;A</li></ul>
  <h5 style="left:873px">Contact Us</h5>
  <div class="contact-row" style="top:140px"><svg width="12" height="14" viewBox="0 0 12 14"><path d="M6 13S1 8 1 5a5 5 0 0110 0c0 3-5 8-5 8z" fill="#fff"/><circle cx="6" cy="5" r="1.8" fill="#0a4ea3"/></svg><span>Lorem ipsum dolor sit amet, consectetur</span></div>
  <div class="contact-row" style="top:217px"><svg width="13" height="13" viewBox="0 0 13 13"><path d="M3 1l2 3-1.5 1.5a7 7 0 004 4L9 8l3 2-1 2C6 12 1 7 1 2z" fill="#fff"/></svg><span>+1 888 888 8888</span></div>
  <div class="contact-row" style="top:268px"><svg width="13" height="11" viewBox="0 0 13 11"><rect x="0" y="0" width="13" height="11" rx="1" fill="#fff"/><path d="M1 1l5.5 5L12 1" stroke="#0a4ea3" stroke-width="1.3" fill="none"/></svg><span>info@companyname.com</span></div>
  <p class="copyright">© Copyrights 2022 Brightmoor Talent | All Rights reserved</p>
</footer>

</body>
</html>
```